Tech business card design

We need an amazing business card design for our new business 'Pexla' a marketing tech startup based in Sydney, Australia. We provide an online marketplace for businesses to search and buy advertising media, connect with service providers and learn more about marketing. We wish to communicate 'cool tech', reliability and professionalism and design based around our logo.

Target Market(s)

Business Owners

Contact Information for Business Card

Name
Position
Email Address
Website
Phone Number

Font styles to use
Other font styles liked:
• Avenir & Avenir Next

Colors

Designer to choose colors to be used in the design.

```html
<!DOCTYPE html>
<html lang="en">
<head>
<meta charset="utf-8">
<title>Pexla Business Card</title>
<link href="https://fonts.googleapis.com/css2?family=Rubik:wght@400;500;700;800&display=swap" rel="stylesheet">
<style>
  :root {
    --navy: #15164a;
    --white: #ffffff;
    --page: #e9eaee;
    --muted: #8a8a96;
    --card-w: 620px;
    --card-h: 354px;
  }
  * { box-sizing: border-box; margin: 0; padding: 0; }
  html, body {
    width: 1200px; height: 912px; overflow: hidden;
    background: var(--page);
    font-family: "Rubik", sans-serif;
  }
  .sheet { position: relative; width: 1200px; height: 912px; }
  .card {
    position: absolute;
    width: var(--card-w); height: var(--card-h);
    border-radius: 18px; overflow: hidden;
    box-shadow: 0 10px 30px rgba(20, 22, 60, 0.18);
  }
  .card-front { left: 290px; top: 80px; background: var(--navy); }
  .card-back { left: 290px; top: 478px; background: var(--white); }

  .wordmark {
    position: absolute;
    font-weight: 800;
    letter-spacing: -2px;
    line-height: 1;
  }
  .wordmark sup { font-size: 11px; font-weight: 500; letter-spacing: 0; margin-left: 4px; vertical-align: top; }
  .card-front .wordmark { color: var(--white); font-size: 110px; left: 128px; top: 110px; }
  .card-back .wordmark { color: var(--navy); font-size: 66px; right: 40px; top: 34px; }

  .contact-band {
    position: absolute; left: 0; right: 0; bottom: 0; height: 140px;
    background: var(--navy); color: var(--white);
  }
  .person { position: absolute; left: 34px; top: 166px; }
  .person-name { font-size: 22px; font-weight: 500; color: var(--navy); }
  .person-title { font-size: 14px; color: var(--muted); margin-top: 2px; }
  .divider {
    position: absolute; left: 150px; right: 40px; top: 208px;
    height: 2px; background: var(--navy);
  }
  .contact-list { position: absolute; left: 34px; top: 20px; list-style: none; }
  .contact-list li { display: flex; align-items: center; gap: 12px; font-size: 16px; line-height: 27px; }
  .contact-list svg { width: 12px; height: 12px; fill: none; stroke: var(--white); stroke-width: 1.6; }
  .address { position: absolute; right: 34px; top: 18px; text-align: right; font-size: 15px; line-height: 24px; }
</style>
</head>
<body>
<main class="sheet">
  <section class="card card-front" aria-label="Card front">
    <div class="wordmark">Pexla<sup>TM</sup></div>
  </section>

  <section class="card card-back" aria-label="Card back">
    <div class="wordmark">Pexla<sup>TM</sup></div>
    <div class="person">
      <p class="person-name">Daniel Harper</p>
      <p class="person-title">Director</p>
    </div>
    <div class="divider"></div>
    <div class="contact-band">
      <ul class="contact-list">
        <li><svg viewBox="0 0 12 12"><path d="M2 1.5l2 0 1 2.5-1.3 1a6 6 0 0 0 3.3 3.3l1-1.3 2.5 1 0 2A1 1 0 0 1 9.5 11 8.5 8.5 0 0 1 1 2.5 1 1 0 0 1 2 1.5z"/></svg>+612 4180-3926</li>
        <li><svg viewBox="0 0 12 12"><rect x="1" y="2.5" width="10" height="7"/><path d="M1 2.5l5 4 5-4"/></svg>info@pexla.com</li>
        <li><svg viewBox="0 0 12 12"><circle cx="6" cy="6" r="5"/><path d="M1 6h10M6 1c2.5 2.8 2.5 7.2 0 10M6 1c-2.5 2.8-2.5 7.2 0 10"/></svg>www.pexla.com</li>
      </ul>
      <p class="address">218 Kelvin Lane<br>Sydney, NSW 2000</p>
    </div>
  </section>
</main>
</body>
</html>
```